Emerging Australian photographer

I'm based in Cunderdin, a small rural town in the Wheatbelt area of Western Australia. So its a good thing that I love to travel further afield both for pleasure and for work. To me that is one and the same thing in any event!

My desire is to take photos that make the viewers heart skip. I love taking photos of people doing the things they love or being with the people they love. For me, the joy of photography comes with capturing the 'moments between the moments'. I like candid photography best of all - like when the new husband is staring joyfully at his bride and at that minute is unaware of the photographer capturing the moment.

I am available for weddings, engagements, birthdays, special events, newborns, family or individual portraits. By the end of the year I will be accredited with the Southern Guild of Accredited Image Makers.

I need a card that stands out but is elegant and would sit well on the table at a wedding or be given out in the church grounds. Classy and a little bit sassy.

Target Market(s)

Consumers who are seeking photographic services, eg wedding guests who see me at work and make enquiries.

Industry/Entity Type

Church

Contact Information for Business Card

Tamsin Everly Photography
Tamsin Everly
0452 306 718
www.tamsineverly-studio.com.au
photos@tamsineverly-studio.com.au

Requirements
Must have
• Must fit with the theme in the watermarks, but be crisp and modern.
Nice to have
• However it's not essential to have the pink! Chatterly and Pipsqueak logos.
Should not have
• Old style fonts like times new roman.

```html
<!DOCTYPE html>
<html lang="en">
<head>
<meta charset="utf-8">
<title>Tamsin Everly Photography – Business Card</title>
<link rel="stylesheet" href="https://fonts.googleapis.com/css2?family=Didact+Gothic&display=swap">
<style>
  :root {
    --backdrop: #ece9e4;
    --card: #f7f7f7;
    --card-edge: #dcdcdc;
    --ink: #6b6b6d;
    --ink-soft: #8a8a8c;
    --mark: #6e6f71;
    --chip: #a9a9ab;
    --blush: #e9a3b8;
  }
  * { box-sizing: border-box; margin: 0; padding: 0; }
  html, body { width: 1200px; height: 1000px; overflow: hidden; }
  body {
    background: var(--backdrop);
    font-family: "Didact Gothic", "Century Gothic", sans-serif;
    color: var(--ink);
    position: relative;
  }
  .card {
    position: absolute;
    background: radial-gradient(circle at 50% 40%, #ffffff 0%, var(--card) 60%, #efefef 100%);
    border: 1px solid var(--card-edge);
    box-shadow: 0 10px 28px rgba(0,0,0,0.12);
  }
  /* Front: portrait */
  .card-front {
    left: 110px; top: 180px;
    width: 380px; height: 640px;
    display: flex; flex-direction: column; align-items: center;
    padding-top: 54px;
  }
  .brand-name {
    font-weight: 400;
    font-size: 46px; letter-spacing: 0.5px; line-height: 1;
    color: var(--ink);
  }
  .brand-tag {
    font-size: 14px; letter-spacing: 7px; margin-top: 4px;
    align-self: flex-end; margin-right: 40px;
    color: var(--ink-soft);
  }
  .brand-mark { margin-top: 30px; }
  .contact {
    margin-top: 36px; text-align: center;
    display: flex; flex-direction: column; align-items: center; gap: 10px;
  }
  .contact-phone { font-size: 26px; letter-spacing: 2px; }
  .contact-email { font-size: 19px; }
  .contact-web { font-size: 13px; color: var(--ink-soft); }
  .social {
    margin-top: 26px; display: flex; gap: 18px;
  }
  .social-item {
    display: flex; align-items: center; gap: 6px;
    font-size: 13px; color: var(--ink-soft);
  }
  .social-chip {
    width: 20px; height: 20px; border-radius: 4px; background: var(--chip);
  }
  /* Back: landscape */
  .card-back {
    left: 560px; top: 300px;
    width: 560px; height: 360px;
    display: flex; flex-direction: column; align-items: center; justify-content: center;
  }
  .back-lockup {
    display: flex; align-items: center; gap: 14px;
  }
  .back-dot {
    width: 10px; height: 10px; border-radius: 50%; background: var(--blush);
  }
  .back-name {
    font-size: 28px; letter-spacing: 3px; color: var(--ink);
  }
</style>
</head>
<body>
  <section class="card card-front" aria-label="Business card front">
    <h1 class="brand-name">Tamsin Everly</h1>
    <p class="brand-tag">Photography</p>
    <svg class="brand-mark" width="240" height="240" viewBox="0 0 240 240" role="img" aria-label="Studio emblem area">
      <circle cx="120" cy="120" r="118" fill="var(--mark)"/>
    </svg>
    <div class="contact">
      <p class="contact-phone">0452 306 718</p>
      <p class="contact-email">photos@tamsineverly-studio.com.au</p>
      <p class="contact-web">www.tamsineverly-studio.com.au</p>
    </div>
    <div class="social">
      <span class="social-item"><span class="social-chip"></span>Pipsqueak</span>
      <span class="social-item"><span class="social-chip"></span>Chatterly</span>
    </div>
  </section>

  <section class="card card-back" aria-label="Business card back">
    <div class="back-lockup">
      <span class="back-dot"></span>
      <p class="back-name">tamsin everly photography</p>
    </div>
  </section>
</body>
</html>
```